Business Card for Inovative Flexible Packaging Company

Create a business card that is both simple and stricking at the same time.
Preferably only one color (orange) or two colors (black and orange).
Information to print:
Lumtrex, Lda
[T] 22 418 6095
[M] 91 362 7148
[F] 22 418 6037
[@] lumtrex.ac@mailvora.com
SEDE & ARMAZÉM
Rua Das Figueiras do Monte, 317
Serzedo
4415-238 Serzedo - VN Gaia
PORTUGAL
Reason: A lot of the ideas are obvious. I want something different. Inovative. dare to do something eye catching with style.
Target Market(s)
Business Consumers. Packaging Designers.
Industry/Entity Type
Business
Look and feel
Each slider illustrates characteristics of the customer's brand and the style your logo design should communicate.

```html
<!DOCTYPE html>
<html lang="pt">
<head>
<meta charset="utf-8">
<title>Lumtrex – Business Card</title>
<link rel="stylesheet" href="https://fonts.googleapis.com/css2?family=Poppins:wght@600&family=Tinos:wght@400&display=swap">
<style>
  :root {
    --orange: #f2480f;
    --black: #0a0a0b;
    --white: #ffffff;
    --ink: #1a1a1a;
    --shadow: rgba(0,0,0,0.45);
  }
  * { margin: 0; padding: 0; box-sizing: border-box; }
  html, body { width: 1200px; height: 900px; overflow: hidden; background: var(--white); }
  .board { position: relative; width: 1200px; height: 900px; background: var(--white); }

  .card {
    position: absolute; top: 177px; width: 540px; height: 312px;
    box-shadow: 6px 6px 8px var(--shadow);
    overflow: hidden;
  }
  .card--front { left: 52px; background: var(--black); }
  .card--back  { left: 633px; background: var(--white); }

  .brand { position: absolute; display: flex; align-items: center; }
  .brand__dot { background: var(--orange); border-radius: 50%; flex: none; }
  .brand__name {
    font-family: "Poppins", sans-serif; font-weight: 600; color: var(--orange);
    line-height: 1; letter-spacing: -0.01em;
  }

  .card--front .brand { left: 116px; top: 116px; }
  .card--front .brand__dot { width: 58px; height: 58px; margin-right: 22px; }
  .card--front .brand__name { font-size: 56px; }

  .card--back .brand { left: 22px; top: 22px; }
  .card--back .brand__dot { width: 46px; height: 46px; margin-right: 12px; }
  .card--back .brand__name { font-size: 38px; }

  .stripes { position: absolute; left: 0; top: 0; width: 540px; height: 312px; }

  .company {
    position: absolute; left: 42px; top: 128px;
    font-family: "Tinos", serif; font-size: 18px; color: var(--ink);
  }
  .contacts { position: absolute; left: 42px; top: 164px; list-style: none; }
  .contacts li {
    display: flex; align-items: center; height: 23px;
    font-family: "Tinos", serif; font-size: 15px; color: var(--ink);
  }
  .contacts svg { width: 13px; height: 13px; margin-right: 6px; fill: var(--orange); flex: none; }

  .address {
    position: absolute; left: 274px; top: 154px;
    font-family: "Tinos", serif; font-size: 15px; line-height: 20px; color: var(--ink);
    font-style: normal;
  }

  .board > .brand { right: 28px; top: 787px; }
  .board > .brand .brand__dot { width: 76px; height: 76px; margin-right: 28px; }
  .board > .brand .brand__name { font-size: 74px; }
</style>
</head>
<body>
<main class="board">

  <section class="card card--front" aria-label="Front of business card">
    <div class="brand"><span class="brand__dot"></span><span class="brand__name">lumtrex</span></div>
  </section>

  <section class="card card--back" aria-label="Back of business card">
    <svg class="stripes" viewBox="0 0 540 312" aria-hidden="true">
      <polygon points="0,0 370,0 362,7 0,7" fill="var(--black)"/>
      <polygon points="0,9 352,9 340,15 0,15" fill="var(--orange)"/>
      <polygon points="196,294 540,294 540,299 188,299" fill="var(--orange)"/>
      <polygon points="176,301 540,301 540,307 166,307" fill="var(--black)"/>
    </svg>

    <div class="brand"><span class="brand__dot"></span><span class="brand__name">lumtrex</span></div>

    <p class="company">Lumtrex, Lda</p>
    <ul class="contacts">
      <li><svg viewBox="0 0 16 16"><path d="M4 1l3 3-2 2c1 2 3 4 5 5l2-2 3 3-2 3C7 15 1 9 1 3z"/></svg>22 418 6095</li>
      <li><svg viewBox="0 0 16 16"><path d="M4 0h8v16H4zM5.5 2v9h5V2zM7 13h2v1.5H7z" fill-rule="evenodd"/></svg>91 362 7148</li>
      <li><svg viewBox="0 0 16 16"><path d="M4 1h7v4H4zM1 6h14v9H1zM3 8h2v2H3zM7 8h2v2H7zM11 8h2v2h-2z" fill-rule="evenodd"/></svg>22 418 6037</li>
      <li><svg viewBox="0 0 16 16"><path d="M1 3h14v10H1zM1 3l7 6 7-6" /></svg>lumtrex.ac@mailvora.com</li>
    </ul>

    <address class="address">
      SEDE &amp; ARMAZÉM<br>
      Rua Das Figueiras do Monte, 317<br>
      Serzedo<br>
      4415-238 Serzedo - VN Gaia<br>
      PORTUGAL
    </address>
  </section>

  <div class="brand"><span class="brand__dot"></span><span class="brand__name">lumtrex</span></div>

</main>
</body>
</html>
```